Velvet Meadow Hamper company needs a brochure design

We need a brochure design for a new company in Dubai called 'Velvet Meadow Hampers'. We already have a logo designed which I have attached and would like to use this and the green/gold/white colours for our brochure. Our company initially will be supplying Velvet Meadow Hamper wear of traditional wicker baskets in many designs which hold all the cutlery, crockery and accessories. We will also be selling picnic accessories. We want to purvey a sense of luxury and class in line with our logo. I have attached some photos of the picnicwear. As our products are changing all the time I thought a fold out cover which stays the same and then product cards inserted into the folder which can be changed according to our product changes. I am looking for a fairly simple design and each product card should have at least one photo of the product on it with a spec and description also. On the cover of the folder I would like room to write about the company and what we do, this can be inside or out and may or may not include photos. I have the logo designs in illustrator format and pdf. Please contact if any more information is needed.
Updates

Reason: I have extended this deadline as there are some content changes taking place.

Industry/Entity Type

It Company

```html
<!DOCTYPE html>
<html lang="en">
<head>
<meta charset="utf-8">
<title>Velvet Meadow Hampers – Tartan Picnic Blanket Product Card</title>
<link rel="stylesheet" href="https://fonts.googleapis.com/css2?family=Montserrat:wght@600&family=Gelasio:wght@400&display=swap">
<style>
  :root {
    --forest: #1b3019;
    --gold: #c9a23a;
    --gold-soft: #b8943a;
    --ivory: #f4f1e6;
    --page: #ffffff;
    --tartan-navy: #1f2a5a;
    --tartan-green: #1d4a3a;
    --bronze: #6b2a1a;
    --heading-font: "Montserrat", Arial, sans-serif;
    --body-font: "Gelasio", Georgia, serif;
  }
  * { margin: 0; padding: 0; box-sizing: border-box; }
  html, body { width: 1200px; height: 1000px; overflow: hidden; background: var(--page); }
  .canvas { position: relative; width: 1200px; height: 1000px; }

  .card { position: absolute; top: 150px; width: 493px; height: 700px; background: var(--forest); overflow: hidden; }
  .card--front { left: 100px; }
  .card--back { left: 607px; }

  /* front card */
  .brand-band { position: absolute; left: 0; top: 0; width: 100%; height: 146px; }
  .brand-mark { position: absolute; left: 50%; top: 46px; transform: translateX(-50%); width: 10px; height: 10px; border-radius: 50%; background: var(--gold); }
  .brand-name { position: absolute; left: 0; top: 64px; width: 100%; text-align: center; font-family: var(--heading-font); font-weight: 600; font-size: 12px; letter-spacing: 2.4px; color: var(--gold); text-transform: uppercase; }
  .brand-rule { position: absolute; left: 180px; top: 81px; width: 133px; height: 1px; background: var(--gold); }
  .flourish { position: absolute; background: var(--gold); opacity: 0.35; border-radius: 2px; }
  .flourish--brand { left: 218px; top: 84px; width: 56px; height: 16px; }

  .foil-strip { position: absolute; left: 0; width: 100%; height: 7px; }
  .foil-strip--top { top: 146px; background: linear-gradient(90deg, var(--bronze) 0%, #8a5a28 25%, var(--gold) 55%, #fff6d8 77%, var(--gold) 86%, var(--bronze) 100%); }
  .foil-strip--bottom { top: 513px; background: linear-gradient(90deg, #8a5a28 0%, var(--gold) 12%, #fff6d8 26%, var(--gold) 45%, #8a4a20 75%, var(--bronze) 100%); }

  .product-stage { position: absolute; left: 0; top: 153px; width: 100%; height: 360px; background: var(--page); }
  .product-photo { position: absolute; left: 50px; top: 65px; width: 395px; height: 237px; border-radius: 10px; background: linear-gradient(160deg, var(--tartan-green) 0%, var(--tartan-navy) 55%, #141d40 100%); }

  .product-info { position: absolute; left: 0; top: 520px; width: 100%; height: 180px; }
  .product-title { position: absolute; left: 28px; top: 16px; font-family: var(--heading-font); font-weight: 600; font-size: 25px; letter-spacing: 3px; color: var(--gold); text-transform: uppercase; }
  .product-desc { position: absolute; left: 28px; top: 51px; width: 420px; font-family: var(--body-font); font-size: 11.5px; line-height: 15px; color: var(--ivory); }
  .web-address { position: absolute; left: 0; bottom: 14px; width: 100%; text-align: center; font-family: var(--body-font); font-size: 10px; color: var(--gold); }

  /* back card */
  .overview { position: absolute; left: 0; top: 232px; width: 100%; text-align: center; }
  .flourish--top { left: 218px; top: 233px; width: 56px; height: 18px; }
  .flourish--bottom { left: 218px; top: 448px; width: 56px; height: 18px; }
  .overview-rule { position: absolute; left: 180px; width: 133px; height: 1px; background: var(--gold-soft); }
  .overview-rule--top { top: 253px; }
  .overview-rule--bottom { top: 445px; }
  .overview-title { position: absolute; left: 0; top: 276px; width: 100%; text-align: center; font-family: var(--heading-font); font-weight: 600; font-size: 22px; letter-spacing: 3.5px; color: var(--gold); text-transform: uppercase; }
  .overview-subtitle { position: absolute; left: 0; top: 304px; width: 100%; text-align: center; font-family: var(--body-font); font-size: 15px; letter-spacing: 0.5px; color: var(--gold); text-transform: uppercase; }
  .spec-list { position: absolute; left: 152px; top: 342px; list-style: none; }
  .spec-list li { position: relative; padding-left: 15px; font-family: var(--body-font); font-size: 11px; line-height: 16.5px; color: var(--ivory); }
  .spec-list li::before { content: ""; position: absolute; left: 0; top: 6px; width: 6px; height: 5px; background: var(--gold); }
</style>
</head>
<body>
<main class="canvas">
  <section class="card card--front">
    <header class="brand-band">
      <span class="brand-mark"></span>
      <p class="brand-name">Velvet Meadow Hampers</p>
      <span class="brand-rule"></span>
      <span class="flourish flourish--brand" role="img" aria-label="Gold decorative flourish"></span>
    </header>
    <div class="foil-strip foil-strip--top"></div>
    <div class="product-stage">
      <div class="product-photo" role="img" aria-label="Photo of a folded blue and green tartan picnic blanket in its carrying case with a handle"></div>
    </div>
    <div class="foil-strip foil-strip--bottom"></div>
    <div class="product-info">
      <h1 class="product-title">Tartan Picnic Blanket</h1>
      <p class="product-desc">This classic blue and green check picnic rug has a waterproof backing and folds into its own carrying case, a practical yet stylish look for any picnic.</p>
      <p class="web-address">www.velvetmeadowhampers.com</p>
    </div>
  </section>

  <section class="card card--back">
    <span class="flourish flourish--top" role="img" aria-label="Gold decorative flourish"></span>
    <span class="overview-rule overview-rule--top"></span>
    <h2 class="overview-title">Tartan Picnic Blanket</h2>
    <p class="overview-subtitle">Overview</p>
    <ul class="spec-list">
      <li>Green and blue check colour scheme</li>
      <li>Measurements, 1800 x 1500mm</li>
      <li>Made from polyester fleece</li>
      <li>Waterproof PVC backing.</li>
      <li>Folds into own carrying case</li>
    </ul>
    <span class="overview-rule overview-rule--bottom"></span>
    <span class="flourish flourish--bottom" role="img" aria-label="Gold decorative flourish"></span>
    <p class="web-address">www.velvetmeadowhampers.com</p>
  </section>
</main>
</body>
</html>
```